Business Card - connecting 2 souls and beggining the journey of self discovery

Logo on the front
with tag line

On the back list of services and contact details

Seminars
workshops
Coaching
podcasts

Darren Whitlow
Health & Wellbeing Life Coach
0491 372 615
darren@brightcoreliving.example
brightcoreliving.example

Industry/Entity Type

Life Coaching

Contact Information for Business Card

I like the use of colour from the logo to be used. I'm not a fan of white.

Requirements
Must have
• My tagline: The journey home starts with you
Nice to have
• Use of colour that is in the mind body soul logo

```html
<!DOCTYPE html>
<html lang="en">
<head>
<meta charset="utf-8">
<title>Brightcore Living – Business Card</title>
<link href="https://fonts.googleapis.com/css2?family=Lato:wght@400;700&family=Open+Sans:wght@400&display=swap" rel="stylesheet">
<style>
  :root {
    --backdrop: #3a3a3c;
    --card-white: #ffffff;
    --brand-grey: #808080;
    --ink: #1e1e1e;
    --violet: #7b3fc9;
    --lime: #9ccc3c;
    --mark: #8f5bd0;
  }
  * { margin: 0; padding: 0; box-sizing: border-box; }
  html, body {
    width: 1200px; height: 900px; overflow: hidden;
    background: var(--backdrop);
  }
  .canvas { position: relative; width: 1200px; height: 900px; }

  .card {
    position: absolute; left: 250px; width: 700px; height: 400px;
    background: var(--card-white); overflow: hidden;
    box-shadow: 0 6px 18px rgba(0,0,0,.35);
    font-family: "Lato", sans-serif;
  }
  .card--front { top: 40px; }
  .card--back { top: 470px; }

  .brand {
    display: flex; align-items: center; gap: 14px;
    color: var(--brand-grey); font-family: "Lato", sans-serif;
    font-weight: 700; font-size: 40px; letter-spacing: -1px;
  }
  .brand__dot {
    width: 46px; height: 46px; border-radius: 50%; background: var(--mark);
    flex: none;
  }

  .card--front .brand { position: absolute; top: 110px; left: 0; right: 0; justify-content: center; }
  .services {
    position: absolute; top: 205px; left: 0; right: 0; text-align: center;
    font-family: "Open Sans", sans-serif; font-size: 19px; color: var(--ink);
  }
  .tagline {
    position: absolute; top: 245px; left: 0; right: 0; text-align: center;
    font-family: "Open Sans", sans-serif; font-size: 21px; letter-spacing: 1.5px;
    color: var(--ink); text-transform: uppercase;
  }

  .card--back .brand { position: absolute; top: 70px; left: 60px; }
  .wave { position: absolute; inset: 0; }

  .contact {
    position: absolute; right: 40px; top: 244px; text-align: right; color: var(--card-white);
  }
  .contact__name { color: var(--lime); font-weight: 700; font-size: 28px; line-height: 1.1; }
  .contact__role { font-size: 19px; margin-bottom: 8px; }
  .contact__line {
    display: flex; justify-content: flex-end; align-items: center; gap: 10px;
    font-size: 17px; line-height: 1.45;
  }
  .contact__icon { width: 16px; height: 16px; flex: none; }
</style>
</head>
<body>
<div class="canvas">

  <section class="card card--front">
    <div class="brand"><span class="brand__dot"></span><span class="brand__name">Brightcore Living</span></div>
    <p class="services">Seminars • Workshops • Coaching • Podcasts</p>
    <p class="tagline">The journey home starts with you</p>
  </section>

  <section class="card card--back">
    <svg class="wave" viewBox="0 0 700 400" width="700" height="400" aria-hidden="true">
      <path class="wave__swoosh" d="M-14 260 C 166 330, 486 340, 686 30 L700 12 L700 400 L-14 400 Z" fill="var(--lime)"/>
      <path class="wave__band" d="M0 260 C 180 330, 500 340, 700 30 L700 400 L0 400 Z" fill="var(--violet)" stroke="var(--card-white)" stroke-width="5"/>
    </svg>
    <div class="brand"><span class="brand__dot"></span><span class="brand__name">Brightcore Living</span></div>
    <div class="contact">
      <p class="contact__name">Darren Whitlow</p>
      <p class="contact__role">Health &amp; Wellbeing Life Coach</p>
      <p class="contact__line">0491 372 615
        <svg class="contact__icon" viewBox="0 0 24 24"><path fill="var(--lime)" d="M6.6 10.8a15 15 0 0 0 6.6 6.6l2.2-2.2a1 1 0 0 1 1-.25 11.4 11.4 0 0 0 3.6.57 1 1 0 0 1 1 1V20a1 1 0 0 1-1 1A17 17 0 0 1 3 4a1 1 0 0 1 1-1h3.5a1 1 0 0 1 1 1c0 1.250.2 2.450.57 3.57a1 1 0 0 1-.25 1z"/></svg>
      </p>
      <p class="contact__line">darren@brightcoreliving.example
        <svg class="contact__icon" viewBox="0 0 24 24"><rect x="2" y="5" width="20" height="14" fill="var(--lime)"/><path d="M2 5l10 8 10-8" fill="none" stroke="var(--violet)" stroke-width="1.6"/></svg>
      </p>
      <p class="contact__line">www.brightcoreliving.example
        <svg class="contact__icon" viewBox="0 0 24 24"><circle cx="12" cy="12" r="10" fill="var(--lime)"/><g fill="none" stroke="var(--violet)" stroke-width="1.3"><ellipse cx="12" cy="12" rx="4.5" ry="10"/><path d="M2 12h20M4 7h16M4 17h16"/></g></svg>
      </p>
    </div>
  </section>

</div>
</body>
</html>
```